Lotstallmart.com Webpage Design

Design Brief for lotstallmart.com (Copy of Brief also in attached Word file)

Name of Website- lotstallmart.com (existing logo and look & feel of website to be changed)

Logo - Finalised. The logo files are attached with the brief as “logo.jpeg”. The “Blue- Grey” version of the logo is for use on lighter backgrounds and the “Orange-White” version of the logo is for use on darker backgrounds. (A full Black version of the logo is also attached). Both versions may be used in different parts of the website. All attached files are in .png format.
Status - The website in functional and is undergoing user trials. However, we want to improve the look & feel of the website so at it seems
a. cotemporary,
b. Easy to Navigate
c. professional and
d. Vibrant.

Please visit ‘lotstallmart.com’ to check out the website and its functionalities – please use it only as a reference for the features & functions to be provided, however the designer should use a ‘Free Hand’ in designing the composition of various parts of the webpage without getting too influenced by the existing design

Objective of the Website ‘lotstallmart.com –
a. It is a portal focussed on listing of ‘Retail’ specific real-estate properties by developers, owners and realty brokers. The properties shall listed under the following four categories-
i. Retail Malls
ii. Shopping Complexes
iii. High-street shops
iv. Retail Warehouses
*refer lotstallmart.com for better clarity

b. The abovementioned properties shall be listed either for ‘Sale’ or ‘rent\lease’ or both

c. Users shall visit the site in case they wish to acquire a retail \ shop space either on ‘sale’ or ‘rent’. These Users would be able to specify the ‘Search Criteria’ through the tool-bars provided on the website – the ‘Search Criteria’ shall comprise of ‘Type of space category’, ‘City’, ‘Locality’, transaction type ie ‘Rent \ Sale’ and ‘Area Range’

d. The main revenue model for the website shall be listing fee ( or advertising charges ) payable by those listing their properties on the website.

Three Main Pages of Website (lotstallmart.com) that need to be designed -
a. Main Home Page (visit the web link - http://lotstallmart.com/ ) - The main home page has the “Search Toolbar” for specifying of Search Criteria by the User. It shall also have the following features & functions-
i. Main Advertising Banner
ii. Featured Projects
iii. New Launches
iv. Toolbar with buttons – ‘Advertise with Us’, ‘Listings Alert’, ‘Mart Wizards’, ‘Advertiser Login’

b. Property Listings Page (visit the web link - http://lotstallmart.com/gurgaon-in-india ) - The List of property options that match the Criteria specified by the ‘User’ get displayed on this page.

c. Property Detail Page - When the ‘User’ clicks on the “More….” Button on the ‘Property Listings Page’ (given in point b. above) the web page with the details of the property opens. (For Example – visit the web link - http://lotstallmart.com/vorne-Shopping-Complex-vorne-quadrion-gurgaon-636 )

Note:- Please refer to attached ‘Shopping’ related images the designer may use them on the website to provide a look & feel of retail if required – either separately or rotate in a single window

Target Market(s)

Retailers & Investors looking for retail space, Real Estate Brokers, Developers

Industry/Entity Type

Advertising

Number of Pages Required

3 page

Requirements
Must have
• Refer to existing site lotstallmart.com -- all the existing functionalities are a must have.
Nice to have
• The Designer may use the retail related images on the website if required for making it more vibrant. Refer attached images Shopping(1-6).jpg

```html
<!DOCTYPE html>
<html lang="en">
<head>
<meta charset="utf-8">
<title>Lotstallmart.com – Home</title>
<link href="https://fonts.googleapis.com/css2?family=Open+Sans:wght@400;600;700&display=swap" rel="stylesheet">
<style>
:root{
  --orange:#f5a623;
  --orange-dark:#e08b12;
  --blue:#1a8fe3;
  --blue-dark:#0b74c9;
  --ink:#333;
  --muted:#666;
  --header:#2b3039;
  --footer:#1f2630;
  --panel:#eef0f2;
  --section-grey:#f1f1f1;
  --white:#fff;
}
*{box-sizing:border-box;margin:0;padding:0}
html,body{width:1200px;height:2956px;overflow:hidden}
body{position:relative;font-family:"Open Sans",Arial,sans-serif;color:var(--ink);background:var(--white)}
.abs{position:absolute}

/* city bar */
.city-bar{left:0;top:0;width:1200px;height:32px;background:var(--orange);color:#fff;font-size:15px;font-weight:600;text-align:center;line-height:32px}

/* header */
.site-header{left:0;top:32px;width:1200px;height:126px;background:var(--header)}
.brand{left:112px;top:72px;display:flex;align-items:center;gap:10px}
.brand-dot{width:30px;height:30px;border-radius:50%;background:var(--orange)}
.brand-name{font-size:30px;font-weight:700;color:#fff;line-height:1}
.brand-tag{left:152px;top:108px;font-size:9px;color:#bbb;letter-spacing:1px}
.nav-item{top:84px;color:var(--orange);font-size:17px;line-height:1.15}
.nav-item small{display:block;color:#ddd;font-size:11px}
.home-icon{left:426px;top:82px}
.list-prop{left:937px;top:56px;color:#eee;font-size:14px}
.btn-login{left:937px;top:80px;width:152px;height:36px;background:var(--orange-dark);color:#fff;font-size:14px;font-weight:700;text-align:center;line-height:36px;border-radius:3px}
.register{left:937px;top:120px;color:var(--orange);font-size:12px}

/* hero */
.hero-photo{left:0;top:158px;width:760px;height:587px;background:linear-gradient(120deg,#c9b7a3 0%,#8f8a86 40%,#5b6f88 70%,#c4b8ab 100%)}
.hero-caption{left:130px;top:638px;width:586px;height:58px;border-radius:29px;background:rgba(30,35,45,.8);display:flex;align-items:center;padding-left:18px;gap:14px;color:var(--orange);font-size:25px;font-weight:600}
.search-panel{left:760px;top:158px;width:440px;height:587px;background:var(--panel)}
.stay{left:780px;top:170px;font-size:20px;color:var(--blue);font-weight:600;display:flex;gap:8px;align-items:center}
.soc{display:inline-block;width:40px;height:16px;background:#d0d6de;border-radius:2px}
.ps-title{left:780px;top:210px;font-size:20px;font-weight:600;color:#222}
.check{font-size:11px;color:#333;display:flex;align-items:center;gap:6px}
.check i{width:10px;height:10px;border:1px solid #999;background:#fff;display:inline-block}
.field-label{left:788px;font-size:14px;font-weight:600;color:#333}
.field{left:788px;width:292px;height:42px;border-radius:21px;background:#fff;font-size:14px;color:#555;line-height:42px;padding-left:18px}
.btn-search{left:836px;top:654px;width:174px;height:44px;border-radius:22px;background:var(--blue);color:#fff;font-size:21px;font-weight:700;text-align:center;line-height:44px}

/* categories */
.cat{top:790px;width:250px;text-align:center}
.cat h3{font-size:19px;font-weight:700;color:#222;margin-top:12px}
.cat p{font-size:15px;color:var(--muted)}

/* listing sections */
.band-grey{left:0;top:991px;width:1200px;height:536px;background:var(--section-grey)}
.sec-title{width:1200px;text-align:center;font-size:26px;font-weight:700;color:var(--blue)}
.sec-title span{font-size:15px;color:#555;font-weight:600;margin-left:10px}
.card{width:228px;text-align:center}
.card-img{position:relative;width:228px;height:168px}
.tag{position:absolute;right:0;top:0;height:30px;padding:0 10px 0 32px;color:#fff;font-size:17px;font-weight:600;line-height:30px;background:var(--blue);clip-path:polygon(24px 0,100% 0,100% 100%,0 100%,0 0)}
.card h4{font-size:19px;font-weight:600;color:var(--blue);margin-top:10px;white-space:nowrap}
.card .loc{font-size:23px;color:#555;line-height:1.3}
.card .kind{font-size:19px;color:#5bb5ef}
.btn-view{display:inline-block;margin-top:14px;width:222px;height:50px;border:1px solid var(--orange);border-radius:25px;color:var(--orange);font-size:16px;line-height:48px;background:#fff}
.view-link{display:block;margin-top:6px;color:var(--orange);font-size:16px}
.arrow{width:30px;height:54px}

/* lower columns */
.band-lower{left:0;top:1980px;width:1200px;height:538px;background:var(--section-grey)}
.col-title{font-size:24px;font-weight:700;color:#222}
.col-rule{height:1px;background:#ccc}
.divider{width:1px;background:#ccc}
.pill{height:32px;border-radius:16px;background:#fff;font-size:14px;color:#666;line-height:32px;padding-left:18px}
.note{font-size:13px;color:#444}
.btn-blue{height:34px;border-radius:17px;background:var(--blue);color:#fff;font-size:15px;font-weight:700;text-align:center;line-height:34px}
.small-text{font-size:14px;color:#333;line-height:1.45}

/* footer */
.site-footer{left:0;top:2518px;width:1200px;height:438px;background:var(--footer)}
.f-title{font-size:20px;font-weight:600;color:var(--blue)}
.f-list{list-style:none;font-size:14px;color:#ddd;line-height:23px}
.f-list li::before{content:"› ";color:#aaa}
.f-text{font-size:14px;color:#ddd;line-height:22px}
.f-orange{color:var(--orange)}
.sq{display:inline-block;width:22px;height:22px;background:#2f7fc8;margin-right:5px}
.copy{left:112px;top:2896px;font-size:12px;color:var(--blue)}
.f-brand{left:902px;top:2880px;display:flex;align-items:center;gap:8px}
</style>
</head>
<body>

<div class="abs city-bar">Bangalore | Chennai | Greater Noida | Gurgaon | Hyderabad | Jaipur | Khanna | Kolkatta | Mumbai | Noida | Pune | Surat |</div>

<header class="abs site-header"></header>
<div class="abs brand"><span class="brand-dot"></span><span class="brand-name">lotstallmart</span></div>
<div class="abs brand-tag">INDIA'S LEADING PORTAL FOR RETAIL SPACE</div>
<svg class="abs home-icon" width="22" height="22" viewBox="0 0 22 22"><path d="M2 11 L11 3 L20 11 M5 9 V19 H17 V9" fill="none" stroke="#f5a623" stroke-width="2"/></svg>
<div class="abs nav-item" style="left:468px">Advertise with us<small>Standard listing - FREE</small></div>
<div class="abs nav-item" style="left:628px">Mart Wizards<small>Shop Search Services</small></div>
<div class="abs nav-item" style="left:794px;top:94px">Listing Alert</div>
<div class="abs list-prop">List Your Property Here</div>
<div class="abs btn-login">ADVERTISER LOGIN</div>
<div class="abs register">New Advertiser - Register</div>

<div class="abs hero-photo" role="img" aria-label="Photo of a smiling young couple carrying shopping bags in a mall"></div>
<div class="abs hero-caption">
  <svg width="34" height="34" viewBox="0 0 34 34"><circle cx="17" cy="17" r="15" fill="none" stroke="#1a8fe3" stroke-width="3"/><path d="M9 17 L15 23 L25 11" fill="none" stroke="#1a8fe3" stroke-width="3"/></svg>
  Velorin 70 Arcade Walk Gurgaon
</div>

<aside class="abs search-panel"></aside>
<div class="abs stay">Stay connected <span class="soc"></span><span class="soc" style="width:28px"></span><span class="soc"></span></div>
<div class="abs ps-title">
  <svg width="18" height="18" viewBox="0 0 18 18"><circle cx="7" cy="7" r="5.5" fill="none" stroke="#222" stroke-width="2"/><path d="M11 11 L16 16" stroke="#222" stroke-width="2.5"/></svg>
  Property Search</div>
<div class="abs check" style="left:786px;top:258px"><i></i>Retail Malls</div>
<div class="abs check" style="left:946px;top:258px"><i></i>Shopping Complex</div>
<div class="abs check" style="left:786px;top:284px"><i></i>High street Rehops</div>
<div class="abs check" style="left:946px;top:284px"><i></i>Retail Warehouses</div>
<div class="abs field-label" style="top:328px">Sale Or Rent Or Both:</div>
<div class="abs field" style="top:354px">Both</div>
<div class="abs field-label" style="top:408px">Select City</div>
<div class="abs field" style="top:434px">--Select--</div>
<div class="abs field-label" style="top:486px">Select City</div>
<div class="abs field" style="top:512px">--Select--</div>
<div class="abs field-label" style="top:564px">Enter Keywords:</div>
<div class="abs field" style="top:588px">Name of Project, Developer etc</div>
<div class="abs btn-search">SEARCH</div>

<section>
  <div class="abs cat" style="left:78px">
    <svg width="80" height="80" viewBox="0 0 80 80"><circle cx="34" cy="42" r="20" fill="none" stroke="#1a8fe3" stroke-width="7"/><path d="M49 57 L66 74" stroke="#1a8fe3" stroke-width="9" stroke-linecap="round"/><rect x="24" y="20" width="20" height="22" fill="none" stroke="#555" stroke-width="3"/></svg>
    <h3>Retail Malls</h3><p>Centrally Air-Conditioned</p></div>
  <div class="abs cat" style="left:344px">
    <svg width="80" height="80" viewBox="0 0 80 80"><circle cx="34" cy="42" r="20" fill="none" stroke="#1a8fe3" stroke-width="7"/><path d="M49 57 L66 74" stroke="#1a8fe3" stroke-width="9" stroke-linecap="round"/><path d="M14 14 H22 L28 38 H50 L54 22 H24" fill="none" stroke="#555" stroke-width="3"/></svg>
    <h3>Shopping Complex</h3><p>Non Air-Conditioned Building</p></div>
  <div class="abs cat" style="left:612px">
    <svg width="80" height="80" viewBox="0 0 80 80"><circle cx="34" cy="42" r="20" fill="none" stroke="#1a8fe3" stroke-width="7"/><path d="M49 57 L66 74" stroke="#1a8fe3" stroke-width="9" stroke-linecap="round"/><path d="M26 44 V20 M34 44 V14 M42 44 V24" stroke="#555" stroke-width="4"/></svg>
    <h3>High Street Shops</h3><p>Road Facing Retail</p></div>
  <div class="abs cat" style="left:878px">
    <svg width="80" height="80" viewBox="0 0 80 80"><circle cx="34" cy="42" r="20" fill="none" stroke="#1a8fe3" stroke-width="7"/><path d="M49 57 L66 74" stroke="#1a8fe3" stroke-width="9" stroke-linecap="round"/><rect x="26" y="14" width="18" height="14" fill="#555" transform="rotate(20 35 21)"/></svg>
    <h3>Retail warehouses</h3><p>Back-end Ratail Storage</p></div>
</section>

<section class="abs band-grey"></section>
<h2 class="abs sec-title" style="left:0;top:1036px">Featured Retail Projects<span>Across India</span></h2>
<svg class="abs arrow" style="left:62px;top:1196px" viewBox="0 0 30 54"><path d="M26 2 L4 27 L26 52" fill="none" stroke="#f5a623" stroke-width="3"/></svg>
<svg class="abs arrow" style="left:1108px;top:1196px" viewBox="0 0 30 54"><path d="M4 2 L26 27 L4 52" fill="none" stroke="#f5a623" stroke-width="3"/></svg>

<div class="abs card" style="left:110px;top:1122px"><div class="card-img" role="img" aria-label="Photo of a glass-fronted shopping complex" style="background:linear-gradient(#9fb6cf,#8a6a52)"><span class="tag">SURAT</span></div><h4>Brevanta</h4><div class="loc">Althan</div><div class="kind">Shopping Complex</div><span class="btn-view">VIEW THE LISTING</span></div>
<div class="abs card" style="left:360px;top:1122px"><div class="card-img" role="img" aria-label="Photo of a busy mall interior atrium" style="background:linear-gradient(#a08060,#5c3f30)"><span class="tag">NOIDA</span></div><h4>Quenta 24K Sohna Road</h4><div class="loc">Sector-81</div><div class="kind">Shopping Complex</div><span class="btn-view">VIEW THE LISTING</span></div>
<div class="abs card" style="left:611px;top:1122px"><div class="card-img" role="img" aria-label="Photo of multi-level mall interior with escalators" style="background:linear-gradient(#c7b9a5,#7a6a5a)"><span class="tag">MOHALI</span></div><h4>The Grand Bazaar Place</h4><div class="loc">Sohna Road</div><div class="kind">Shopping Complex</div><span class="btn-view">VIEW THE LISTING</span></div>
<div class="abs card" style="left:861px;top:1122px"><div class="card-img" role="img" aria-label="Photo of a modern mall tower against a blue sky" style="background:linear-gradient(#3d78c4,#9bb6d6)"><span class="tag">MYSORE</span></div><h4>Linden Mall</h4><div class="loc">Sector 102</div><div class="kind">Shopping Complex</div><span class="btn-view">VIEW THE LISTING</span></div>

<h2 class="abs sec-title" style="left:0;top:1568px">Featured New Launches<span>Across India</span></h2>
<svg class="abs arrow" style="left:62px;top:1710px" viewBox="0 0 30 54"><path d="M26 2 L4 27 L26 52" fill="none" stroke="#f5a623" stroke-width="3"/></svg>
<svg class="abs arrow" style="left:1108px;top:1710px" viewBox="0 0 30 54"><path d="M4 2 L26 27 L4 52" fill="none" stroke="#f5a623" stroke-width="3"/></svg>

<div class="abs card" style="left:110px;top:1642px"><div class="card-img" role="img" aria-label="Photo of a lit mall atrium" style="background:linear-gradient(#6b4a2e,#c8a070)"><span class="tag">BHOPAL</span></div><h4>Orvek Galleria 91</h4><div class="loc">ROHINI</div><div class="kind">RETAIL MALLS</div><span class="view-link">VIEW THE LISTING</span></div>
<div class="abs card" style="left:360px;top:1642px"><div class="card-img" role="img" aria-label="Photo of a mall facade at dusk" style="background:linear-gradient(#1f3b6b,#8c6a3c)"><span class="tag">DELHI</span></div><h4>K7K Metropolitan</h4><div class="loc">NH BYPASS</div><div class="kind">RETAIL MALLS</div><span class="view-link">VIEW THE LISTING</span></div>
<div class="abs card" style="left:611px;top:1642px"><div class="card-img" role="img" aria-label="Photo of a supermarket aisle with shoppers" style="background:linear-gradient(#b89a70,#4d5c3a)"><span class="tag">CHENNAI</span></div><h4>Solvane Mall</h4><div class="loc">KOLAR ROAD</div><div class="kind">RETAIL MALLS</div><span class="view-link">VIEW THE LISTING</span></div>
<div class="abs card" style="left:861px;top:1642px"><div class="card-img" role="img" aria-label="Photo of illuminated shop fronts at night" style="background:linear-gradient(#3a2a20,#b07a4a)"><span class="tag">AGRA</span></div><h4>Orvek One Sky Center</h4><div class="loc">MALLESHWARAM</div><div class="kind">RETAIL MALLS</div><span class="view-link">VIEW THE LISTING</span></div>

<section class="abs band-lower"></section>
<div class="abs divider" style="left:404px;top:2030px;height:460px"></div>
<div class="abs divider" style="left:766px;top:2030px;height:460px"></div>

<h3 class="abs col-title" style="left:108px;top:2018px">Listing Alert</h3>
<div class="abs col-rule" style="left:108px;top:2058px;width:280px"></div>
<svg class="abs" style="left:112px;top:2088px" width="50" height="36" viewBox="0 0 50 36"><rect x="1" y="1" width="48" height="34" fill="#ddd" stroke="#aaa"/><path d="M1 1 L25 20 L49 1" fill="none" stroke="#aaa"/></svg>
<p class="abs note" style="left:176px;top:2086px;width:210px">Suscribe  for Fortnightly Email update on New Listings @ Lotstall-Martspace</p>
<div class="abs pill" style="left:112px;top:2158px;width:256px">Enter your email address;</div>
<div class="abs pill" style="left:112px;top:2208px;width:256px;color:var(--blue)">Select option</div>
<p class="abs note" style="left:118px;top:2246px">(select retail format of interest)</p>
<div class="abs pill" style="left:112px;top:2282px;width:256px">Adilabad</div>
<div class="abs" style="left:338px;top:2286px;width:26px;height:24px;background:var(--blue);border-radius:4px"></div>
<p class="abs note" style="left:118px;top:2320px">(select cities of interest)</p>
<div class="abs btn-blue" style="left:118px;top:2356px;width:116px">SUBSCRIBE</div>

<h3 class="abs col-title" style="left:434px;top:2018px">Editor's Choice</h3>
<div class="abs col-rule" style="left:434px;top:2058px;width:310px"></div>
<div class="abs" role="img" aria-label="Photo of a tall golden-lit tower at sunset" style="left:430px;top:2088px;width:316px;height:212px;background:linear-gradient(#d99a4a,#6a5a4a)"></div>
<p class="abs small-text" style="left:430px;top:2314px;width:316px;font-size:13px">A "Select" Listing of Retail Properties Handpicked by our Editors based on their own positive evaluation on parameters &amp; attributes such as Design Concept, Location, Developer, Success Potential. So Read On to Check Out for yourself ........... ..</p>
<div class="abs btn-blue" style="left:430px;top:2438px;width:114px">MORE</div>

<h3 class="abs col-title" style="left:794px;top:2018px">Mart Wizards</h3>
<div class="abs col-rule" style="left:794px;top:2058px;width:300px"></div>
<p class="abs note" style="left:800px;top:2084px;width:292px;line-height:1.5">Post your Retail Space requirement with us and our experts shall get back with suitable options and even help you in your transaction. This is a Free Service!</p>
<p class="abs note" style="left:800px;top:2180px;font-size:14px">Enter your email address;</p>
<div class="abs pill" style="left:802px;top:2210px;width:284px"></div>
<p class="abs note" style="left:800px;top:2252px;font-size:14px">Enter your email address;</p>
<div class="abs pill" style="left:802px;top:2282px;width:284px"></div>
<p class="abs note" style="left:804px;top:2326px;font-size:14px">Add Description of Reauirement</p>
<div class="abs" style="left:802px;top:2356px;width:276px;height:72px;background:#fff;border-radius:4px"></div>
<div class="abs btn-blue" style="left:806px;top:2444px;width:114px">SEND</div>

<footer class="abs site-footer"></footer>
<h4 class="abs f-title" style="left:112px;top:2562px">About Retail Hubline</h4>
<ul class="abs f-list" style="left:116px;top:2602px"><li>About Us</li><li>Privacy Policy</li><li>Terms of Use</li><li>Contact</li><li>Us Site Map</li></ul>
<ul class="abs f-list" style="left:290px;top:2602px"><li>Retail Malls</li><li>Shopping Complex</li><li>High Street Shops</li><li>Retail Warehouses</li></ul>
<h4 class="abs f-title" style="left:468px;top:2562px">Who We Are</h4>
<p class="abs f-text" style="left:468px;top:2604px;width:342px">Lotstallmart.com - About Us<br>Lotstallmart.com is a Specialised Web based platform for Retail Space, featuring properties across India under various formats such as Retail Malls, Shopping Complexes, High-street Shops. Also featured are "Retail Warehouses" which provide the logistic back-end for the retail business. Lotstallmart.com is useful to various category of users as follows- a. Devel More...</p>
<h4 class="abs f-title" style="left:858px;top:2562px">Contact Us</h4>
<p class="abs f-text" style="left:860px;top:2602px;width:240px">Retail Hubline<br>Suite 218, 2nd Floor,<br>Lorem Ipsum is simply,<br>Block-Q, Gurgaon - 122900</p>
<p class="abs f-text f-orange" style="left:860px;top:2702px">Phone : 000-000-0000<br>Fax : 000 - 000 - 0000</p>
<div class="abs" style="left:864px;top:2756px"><span class="sq"></span><span class="sq"></span><span class="sq"></span><span class="sq"></span><span class="sq"></span></div>
<div class="abs copy">Copyright © 2015 Retail Hubline.com. All rights reserved.</div>
<div class="abs f-brand"><span class="brand-dot" style="background:var(--blue);width:24px;height:24px"></span><span class="brand-name" style="font-size:24px;color:var(--blue)">lotstallmart</span></div>

</body>
</html>
```